Stationery Design Project for Nimbora, Chicago

Nimbora, a street parking application which helps car drivers find a street parking spot by offering an ideal path along which to look for parking. This path is calculated by our algorithm based on data (e.g. historical data, baseball games schedule, etc.). Along this path the driver will find a spot and will also save 70% of the search time. Customer we target is reg. between 21 and 45 yo.

We envision something young, fresh, bright and original. Slightly abstract maybe. It should represent the idea and elements of finding street parking in the city, e.g. car(s), parking spot, people, city, etc. (just ideas!).

Logo is attached.

Requirement:
- Business Cards (2 Sided Full Color CMYK)
- Letterhead (1 Sided Full Color CMYK)
- Envelope (1 Sided Full Color CMYK)
- Sticker (1 Sided Full Color CMYK), round with a 2inch diameter.

Reason: We're starting to get more and more designs and need more time to look into all of them. Very exciting!! Thanks to everybody!

Hi all, we're in the process of selecting our favs. Though choices!!! Really good submissions. Will keep you posted and sorry for the delay.

Target Market(s)

Car drivers and owners between 21 and 45

Industry/Entity Type

Parking

Requirements
Must have
• Sticker should be round and include company URL nimbora.com and the new logo which we will attach soon.
Should not have
• Should not be too serious or boring.

```html
<!DOCTYPE html>
<html lang="en">
<head>
<meta charset="utf-8">
<title>Nimbora business card</title>
<link rel="stylesheet" href="https://fonts.googleapis.com/css2?family=Source+Sans+3:wght@400;600;700&display=swap">
<style>
  :root {
    --backdrop: #d9d9d9;
    --card: #ffffff;
    --brand-blue: #1f3fae;
    --wordmark: #1b1b1b;
    --text: #4a4a4a;
    --text-strong: #555555;
    --rule: #6a6a6a;
    --mist: #f2f3f4;
    --haze: #dfe2e5;
    --asphalt-light: #a9acaf;
    --asphalt: #6e7175;
    --asphalt-dark: #4f5256;
    --car-red: rgba(176, 58, 52, 0.35);
    --car-white: rgba(255, 255, 255, 0.55);
    --car-blue: rgba(70, 90, 140, 0.25);
  }
  * { box-sizing: border-box; margin: 0; padding: 0; }
  html, body {
    width: 956px; height: 1200px; overflow: hidden;
    background: var(--backdrop);
    font-family: "Source Sans 3", "Myriad Pro", Arial, sans-serif;
  }
  .canvas { position: relative; width: 956px; height: 1200px; }
  .card {
    position: absolute; left: 80px; width: 798px; height: 454px;
    background: var(--card); border-radius: 28px; overflow: hidden;
  }
  .card--front { top: 113px; }
  .card--back { top: 643px; }
  .brand {
    position: absolute; left: 122px; top: 55px;
    display: flex; align-items: center; gap: 28px;
  }
  .brand__mark {
    width: 156px; height: 156px; border-radius: 50%;
    background: var(--brand-blue);
  }
  .brand__name {
    font-size: 100px; font-weight: 600; color: var(--wordmark);
    line-height: 1; letter-spacing: 1px;
  }
  .contact {
    position: absolute; left: 0; right: 0; top: 278px;
    text-align: center; color: var(--text);
  }
  .contact__rule {
    display: block; width: 206px; height: 2px; margin: 0 auto;
    background: linear-gradient(90deg, transparent, var(--rule), transparent);
  }
  .contact__name {
    font-size: 28px; font-weight: 700; color: var(--text-strong);
    line-height: 36px; margin: 3px 0 2px;
  }
  .contact__role { font-size: 21px; }
  .contact__line { font-size: 25px; line-height: 37px; }
  .contact__line b { font-weight: 700; }
  .contact__line .gap { display: inline-block; width: 16px; }
  .contact__rule--lower { margin-bottom: 3px; }
  .lot-photo {
    position: absolute; left: 0; right: 0; top: 150px; bottom: 0;
    background:
      linear-gradient(180deg, var(--card) 0%, rgba(255,255,255,0.85) 12%, rgba(255,255,255,0) 38%),
      radial-gradient(ellipse 22% 14% at 42% 78%, var(--car-red), transparent 70%),
      radial-gradient(ellipse 18% 12% at 78% 62%, var(--car-red), transparent 70%),
      radial-gradient(ellipse 25% 14% at 20% 72%, var(--car-white), transparent 70%),
      radial-gradient(ellipse 30% 12% at 60% 55%, var(--car-white), transparent 70%),
      radial-gradient(ellipse 20% 10% at 70% 48%, var(--car-blue), transparent 70%),
      linear-gradient(175deg, var(--mist) 0%, var(--haze) 22%, var(--asphalt-light) 50%, var(--asphalt) 78%, var(--asphalt-dark) 100%);
  }
  .card--back .brand { z-index: 1; }
</style>
</head>
<body>
<div class="canvas">
  <section class="card card--front">
    <div class="brand">
      <div class="brand__mark"></div>
      <div class="brand__name">nimbora</div>
    </div>
    <div class="contact">
      <span class="contact__rule"></span>
      <p class="contact__name">Your Name - <span class="contact__role">Designation</span></p>
      <span class="contact__rule contact__rule--lower"></span>
      <p class="contact__line"><b>t</b> : 123-456-7890<span class="gap"></span><b>c</b> : 123-456-7890</p>
      <p class="contact__line"><b>e</b> : name@website.com<span class="gap"></span><b>w</b> : www.website.com</p>
      <p class="contact__line">City Name, Street Name, State Name, Country Code</p>
    </div>
  </section>

  <section class="card card--back">
    <div class="lot-photo" role="img" aria-label="Misty photograph of a busy city parking lot packed with rows of cars, seen from above"></div>
    <div class="brand">
      <div class="brand__mark"></div>
      <div class="brand__name">nimbora</div>
    </div>
  </section>
</div>
</body>
</html>
```